Coastline Premier Retreats Business Card Design

Design a business card for Coastline Premier Retreats. Look at the website for colors and reference. Card should have logo, name, title, office number, mobile number, email, URL and a tagline like, "Luxury Hotel & Resort Email Marketing" (This might change).

https://www.coastlinepremierretreats.example

The rest I will leave up to your imagination.

Contact Information for Business Card

Logo, name, title, office number, mobile number, email, URL and a tagline like, "Luxury Hotel & Resort Email Marketing" (This might change).

```html
<!DOCTYPE html>
<html lang="en">
<head>
<meta charset="utf-8">
<title>Coastline Premier Retreats – Business Card</title>
<link rel="stylesheet" href="https://fonts.googleapis.com/css2?family=Montserrat:wght@400;500;700;800&display=swap">
<style>
  :root {
    --backdrop: #1c1c1e;
    --card: #28292d;
    --accent: #f26f21;
    --ink: #ffffff;
    --ink-soft: #d9d9d9;
  }
  * { box-sizing: border-box; margin: 0; padding: 0; }
  html, body {
    width: 1200px; height: 900px; overflow: hidden;
    background: var(--backdrop);
    font-family: "Montserrat", Arial, sans-serif;
  }
  .stage { position: relative; width: 1200px; height: 900px; }
  .card {
    position: absolute;
    width: 600px; height: 343px;
    background: var(--card);
    border-radius: 20px;
    border-bottom: 7px solid var(--accent);
    overflow: hidden;
  }
  .card--front { left: 150px; top: 80px; }
  .card--back  { left: 450px; top: 470px; }

  .wordmark {
    display: flex; align-items: center; gap: 14px;
    color: var(--ink);
    font-weight: 800;
    text-transform: uppercase;
    letter-spacing: 1px;
    line-height: 1;
    white-space: nowrap;
  }
  .wordmark__square { width: 18px; height: 18px; background: var(--accent); flex: none; }
  .card--front .wordmark {
    position: absolute; left: 0; right: 0; top: 120px;
    justify-content: center; font-size: 28px;
  }
  .tagline {
    position: absolute; left: 0; right: 0; bottom: 44px;
    text-align: center;
    color: var(--accent);
    font-weight: 700; font-size: 15px;
  }

  .card--back .wordmark { position: absolute; left: 60px; top: 56px; font-size: 26px; }
  .identity { position: absolute; left: 40px; top: 150px; width: 210px; text-align: right; }
  .identity__name { color: var(--accent); font-weight: 700; font-size: 22px; white-space: nowrap; }
  .identity__title { color: var(--ink-soft); font-weight: 400; font-size: 14px; margin-top: 4px; }
  .divider {
    position: absolute; left: 268px; top: 132px;
    width: 2px; height: 100px; background: var(--accent);
  }
  .contacts { position: absolute; left: 286px; top: 134px; list-style: none; }
  .contacts li {
    display: flex; align-items: center; gap: 10px;
    color: var(--ink); font-size: 12.5px; height: 24px; white-space: nowrap;
  }
  .contacts svg { width: 14px; height: 14px; fill: var(--accent); flex: none; }
  .address {
    position: absolute; left: 0; right: 0; bottom: 40px;
    text-align: center; color: var(--ink); font-size: 14px;
  }
</style>
</head>
<body>
<main class="stage">
  <section class="card card--front" aria-label="Card front">
    <div class="wordmark"><span class="wordmark__square"></span>Coastline Premier Retreats</div>
    <p class="tagline">Luxury Hotel &amp; Resort Email Marketing</p>
  </section>

  <section class="card card--back" aria-label="Card back">
    <div class="wordmark"><span class="wordmark__square"></span>Coastline Premier Retreats</div>
    <div class="identity">
      <p class="identity__name">Daniel Okafor</p>
      <p class="identity__title">Owner</p>
    </div>
    <span class="divider"></span>
    <ul class="contacts">
      <li><svg viewBox="0 0 24 24" aria-hidden="true"><path d="M6.6 10.8a15.1 15.1 0 0 0 6.6 6.6l2.2-2.2a1 1 0 0 1 1-.25 11.4 11.4 0 0 0 3.6.57 1 1 0 0 1 1 1V20a1 1 0 0 1-1 1A17 17 0 0 1 3 4a1 1 0 0 1 1-1h3.5a1 1 0 0 1 1 1c0 1.25.2 2.45.57 3.6a1 1 0 0 1-.25 1z"/></svg>555.210.4837 x 318</li>
      <li><svg viewBox="0 0 24 24" aria-hidden="true"><path d="M7 1h10a2 2 0 0 1 2 2v18a2 2 0 0 1-2 2H7a2 2 0 0 1-2-2V3a2 2 0 0 1 2-2zm0 3v14h10V4zm5 15.5a1 1 0 1 0 0 2 1 1 0 0 0 0-2z"/></svg>555.318.2290</li>
      <li><svg viewBox="0 0 24 24" aria-hidden="true"><path d="M2 5h20v14H2zm2 2v.5l8 5 8-5V7zm0 2.9V17h16V9.9l-8 5z"/></svg>info@coastlinepremierretreats.example</li>
      <li><svg viewBox="0 0 24 24" aria-hidden="true"><path d="M12 2a10 10 0 1 0 0 20 10 10 0 0 0 0-20zm6.9 9h-3a15 15 0 0 0-1.3-5.6A8 8 0 0 1 18.9 11zM12 4c.9 1.2 1.8 3.6 1.9 7h-3.8c.1-3.4 1-5.8 1.9-7zM9.4 5.4A15 15 0 0 0 8.1 11h-3a8 8 0 0 1 4.3-5.6zM5.1 13h3a15 15 0 0 0 1.3 5.6A8 8 0 0 1 5.1 13zM12 20c-.9-1.200-1.8-3.6-1.9-7h3.8c-.1 3.4-1 5.8-1.9 7zm2.6-1.4a15 15 0 0 0 1.300-5.6h3a8 8 0 0 1-4.3 5.6z"/></svg>www.coastlinepremierretreats.example</li>
    </ul>
    <p class="address">418 Harbor Ave. Suite 740 Seabrook, CA 95010</p>
  </section>
</main>
</body>
</html>
```